Larkmoor Drones Business Card

We are a new company based in Central Queensland, Australia that uses specalised drones (Voskel Ferra Q80) to undertake mainly agricultural operations, like spraying weeds, spraying crops, spreading seed etc. I have attached a Plimbo proof of a card I was thinking along the lines of - purely a start point. The drone used in the business card MUST be a Voskel Ferra Q80.
I am very open to other ideas, especially fonts and layout. I don't have website etc set up yet.
The images are stock and easily interchangeable, I just ask that any background images reflect the local central Queensland area. The photo of the drone is not even complete (propellers cut off) and I need a new stock photo – I’m not sure if this is an issue, or I can pay for an image if need be. PLEASE FIND AN FERRA Q80 image - 4 sprayers, not 6.
The logo/business name is very draft and looking for further ideas, ideally incorporating drones or agriculture design elements into the design of the business name. The business name needs work on the graphic/design – it is a draft that I have included, the drone propellers (being a different colour) are DRAFT only and intended for changes. PLEASE DO NOT USE THE DRONE PORPELLER I HAVE USED AS A DRAFT. TRY TO FIND SOMETHING ELSE.. The arrow is a shape and not aligned in any way, I would also like ideas on different fonts and additional elements, like air streams, aviation elements, aviation or country western (farming like) themes and fonts etc.
Ideally looking at staying within the blue, green and yellow colours, keeping with an natural, outdoorsy, environmental feel.

Target Market(s)

Farmers, Agriculture, Local Governments, Land Managers

Industry/Entity Type

Agriculture, Drones, Aviation

Contact Information for Business Card

Agricultural Drone (Voskel Ferra Q80), Farming, Business Name.

Font styles to use
Sans Serif

Colors
0054AA
0677BA
7BADD7
CADEEF
E8F1F8
0094D4
00A9DD
6FCCEA
C7EBF8
E9F6FB
00AB8E
00BBA5
67D7C9
C6EFE9
E9F9F6
59FF00
82FF00
B8FF75
E3FFCB
F4FFEA

Requirements
Must have
• Voskel Ferra Q80 Drone
Should not have
• Tractors

```html
<!DOCTYPE html>
<html lang="en">
<head>
<meta charset="utf-8">
<title>Larkmoor Drones Business Card</title>
<link rel="stylesheet" href="https://fonts.googleapis.com/css2?family=Alfa+Slab+One&family=Roboto+Slab:wght@300;500&display=swap">
<style>
  :root {
    --stage: #2b2b2b;
    --leaf: #7c8f3a;
    --leaf-deep: #62752a;
    --leaf-light: #9aad52;
    --zest: #f2ee32;
    --sun: #f0b048;
    --sun-pale: #f8d890;
    --white: #ffffff;
  }
  * { box-sizing: border-box; margin: 0; padding: 0; }
  html, body { width: 1200px; height: 800px; overflow: hidden; background: var(--stage); }
  .canvas { position: relative; width: 1200px; height: 800px; }
  .card {
    position: absolute; left: 280px; width: 640px; height: 366px;
    border-radius: 34px; overflow: hidden; background: var(--leaf);
    box-shadow: 0 10px 30px rgba(0,0,0,.45);
  }
  .card--front { top: 22px; }
  .card--back { top: 412px; }
  .card > svg { position: absolute; inset: 0; width: 100%; height: 100%; }
  .slogan {
    position: absolute; left: 0; right: 0; top: 20px; text-align: center;
    font-family: "Alfa Slab One", serif; font-size: 27px; letter-spacing: 5px;
    color: var(--leaf-deep);
  }
  .brand {
    position: absolute; font-family: "Alfa Slab One", serif; color: var(--white);
    line-height: 1; text-align: center; white-space: nowrap;
  }
  .card--front .brand { left: 300px; width: 280px; top: 222px; font-size: 40px; }
  .tagline {
    position: absolute; font-family: "Roboto Slab", serif; font-weight: 300;
    color: var(--zest); letter-spacing: 1.5px; white-space: nowrap; text-align: center;
  }
  .card--front .tagline { left: 300px; width: 280px; top: 312px; font-size: 14px; }
  .person { position: absolute; left: 34px; top: 100px; color: var(--white); font-family: "Alfa Slab One", serif; }
  .person__name { font-size: 40px; line-height: 1; }
  .person__role { font-size: 17px; margin-top: 6px; margin-left: 16px; }
  .contact { position: absolute; right: 26px; top: 128px; list-style: none; }
  .contact li {
    display: flex; justify-content: flex-end; align-items: center; gap: 10px;
    height: 24px; font-family: "Alfa Slab One", serif; font-size: 14px; color: var(--white);
    text-shadow: 0 1px 3px rgba(40,50,10,.55);
  }
  .contact .icon { width: 19px; height: 19px; flex: none; }
  .card--back .brand { left: 0; right: 0; top: 268px; font-size: 38px; }
  .card--back .tagline { left: 0; right: 0; top: 312px; font-size: 13px; }
</style>
</head>
<body>
<main class="canvas">

  <section class="card card--front" aria-label="Card front">
    <svg viewBox="0 0 640 366" preserveAspectRatio="none">
      <defs>
        <linearGradient id="sky-field" x1="0" y1="0" x2="0" y2="1">
          <stop offset="0" stop-color="#f3c060"/>
          <stop offset=".4" stop-color="#e9c270"/>
          <stop offset=".7" stop-color="#b2b254"/>
          <stop offset="1" stop-color="#8ea23e"/>
        </linearGradient>
        <radialGradient id="drone-front" cx=".5" cy=".45" r=".6">
          <stop offset="0" stop-color="#5a5a48" stop-opacity=".55"/>
          <stop offset=".6" stop-color="#8a8660" stop-opacity=".3"/>
          <stop offset="1" stop-color="#c8b878" stop-opacity="0"/>
        </radialGradient>
      </defs>
      <rect class="photo" width="640" height="200" fill="url(#sky-field)" role="img" aria-label="Photo: Central Queensland crop field at sunset"/>
      <rect class="photo-drone" x="130" y="62" width="380" height="128" rx="20" fill="url(#drone-front)" role="img" aria-label="Photo: Voskel Ferra Q80 agricultural drone with four sprayers spraying the crop"/>
      <rect class="band" y="190" width="640" height="24" fill="var(--zest)"/>
      <rect class="base" y="214" width="640" height="152" fill="var(--leaf)"/>
    </svg>
    <p class="slogan">SPRAY · WEED · SEED · FEED</p>
    <p class="brand">LARKMOOR<br>DRONES</p>
    <p class="tagline">SERVICING CENTRAL QUEENSLAND</p>
  </section>

  <section class="card card--back" aria-label="Card back">
    <svg viewBox="0 0 640 366" preserveAspectRatio="none">
      <defs>
        <linearGradient id="field" x1="1" y1="0" x2=".3" y2="1">
          <stop offset="0" stop-color="#eda842"/>
          <stop offset=".35" stop-color="#c4b460"/>
          <stop offset=".65" stop-color="#93a646"/>
          <stop offset="1" stop-color="#7c8f3a"/>
        </linearGradient>
        <linearGradient id="swoosh" x1="0" y1="1" x2="1" y2="0">
          <stop offset="0" stop-color="var(--zest)"/>
          <stop offset=".55" stop-color="#e9e040"/>
          <stop offset="1" stop-color="var(--sun-pale)"/>
        </linearGradient>
        <radialGradient id="drone-back" cx=".5" cy=".45" r=".6">
          <stop offset="0" stop-color="#5a5a48" stop-opacity=".5"/>
          <stop offset=".6" stop-color="#8a8660" stop-opacity=".25"/>
          <stop offset="1" stop-color="#c8b878" stop-opacity="0"/>
        </radialGradient>
      </defs>
      <rect width="640" height="366" fill="var(--leaf)"/>
      <path class="photo" d="M0,290 C150,285 280,230 340,130 C370,75 430,25 540,0 L640,0 L640,366 L0,366 Z" fill="url(#field)" role="img" aria-label="Photo: green crop field under a golden Central Queensland sky"/>
      <rect class="photo-drone" x="420" y="24" width="180" height="92" rx="16" fill="url(#drone-back)" role="img" aria-label="Photo: Voskel Ferra Q80 drone with four sprayers in flight"/>
      <path class="swoosh" d="M0,238 C150,250 270,205 325,120 C355,70 420,20 530,0 L548,0 C440,25 378,75 348,125 C285,230 150,292 0,290 Z" fill="url(#swoosh)"/>
      <path class="swoosh-line" d="M200,276 C280,240 320,180 350,125 C380,72 430,30 500,8" fill="none" stroke="var(--leaf-deep)" stroke-width="5"/>
    </svg>

    <div class="person">
      <p class="person__name">Maren Tolvik</p>
      <p class="person__role">Founder &amp; CEO</p>
    </div>

    <ul class="contact">
      <li>(07) 4900 2175
        <svg class="icon" viewBox="0 0 20 20"><circle cx="10" cy="10" r="9" fill="var(--white)"/><path d="M6.5,5.5 l2,0 1,2.5 -1.2,1 a6,6 0 0 0 2.7,2.7 l1,-1.2 2.5,1 0,2 a1,1 0 0 1 -1,1 a8,8 0 0 1 -8,-8 a1,1 0 0 1 1,-1z" fill="var(--leaf)"/></svg></li>
      <li>www.larkmoorsite.com
        <svg class="icon" viewBox="0 0 20 20"><circle cx="10" cy="10" r="9" fill="var(--white)"/><g fill="none" stroke="var(--leaf)" stroke-width="1.2"><circle cx="10" cy="10" r="5.5"/><ellipse cx="10" cy="10" rx="2.4" ry="5.5"/><path d="M4.5,10h11"/></g></svg></li>
      <li>info@larkmoorsite.com
        <svg class="icon" viewBox="0 0 20 20"><circle cx="10" cy="10" r="9" fill="var(--white)"/><rect x="5" y="6.5" width="10" height="7" fill="none" stroke="var(--leaf)" stroke-width="1.2"/><path d="M5,6.5 l5,4 5,-4" fill="none" stroke="var(--leaf)" stroke-width="1.2"/></svg></li>
      <li>@larkmoorsite.com
        <svg class="icon" viewBox="0 0 20 20"><circle cx="10" cy="10" r="9" fill="var(--white)"/></svg></li>
      <li>@larkmoorsite.com
        <svg class="icon" viewBox="0 0 20 20"><circle cx="10" cy="10" r="9" fill="var(--white)"/></svg></li>
    </ul>

    <p class="brand">LARKMOOR DRONES</p>
    <p class="tagline">SERVICING CENTRAL QUEENSLAND</p>
  </section>

</main>
</body>
</html>
```